Dietitian needs awesome business card

I need a contemporary design that's eye catching but professional.
My card is to given to doctors, specialists and patients alike.
I manage patients with chronic diseases
I have uploaded my logo and current business card, I would also like the other Certified Clinical Nutritionist logo incorporated into the design

Target Market(s)

Doctors, specialists and patients

Industry/Entity Type

Healthcare

Contact Information for Business Card

www.brightfieldnutrition.com.au
Ph: 0427 561 903
Fax: 6457 2183
email: marcus.k.diet@fernmail.com
Space on the back of the card with: Appointment date, Appointment time and appointment location

Font styles to use
Serif

Colors
fbee3e
876aae
ffc214

Requirements
Must have
• My Logo
• Certified Clinical Nutritionist Logo
• My 4 locations - Pinebrook Medical Centre, North Corrin Health, Hollis Medical, Ashcombe Doctors Surgery
Nice to have
• I like the colours in my current business card

```html
<!DOCTYPE html>
<html lang="en">
<head>
<meta charset="utf-8">
<title>Brightfield Nutrition &amp; Dietetics – Business Card</title>
<link rel="stylesheet" href="https://fonts.googleapis.com/css2?family=Philosopher:ital,wght@0,400;1,400&display=swap">
<style>
  :root {
    --backdrop: #2b2b2b;
    --white: #ffffff;
    --navy: #1f2a80;
    --royal: #1b5fbf;
    --brand-blue: #1e2f8f;
    --leaf: #6cbd2a;
    --leaf-light: #a6d64a;
    --badge: #f47b20;
    --mint: #edf6df;
    --rule: #8a98b8;
    --ink: #1f2a80;
  }
  * { box-sizing: border-box; margin: 0; padding: 0; }
  html, body { width: 1200px; height: 987px; overflow: hidden; }
  body {
    background: var(--backdrop);
    font-family: "Philosopher", Georgia, serif;
    position: relative;
  }
  .card {
    position: absolute;
    width: 525px;
    height: 300px;
    left: 293px;
    transform: scale(1.1714);
    transform-origin: 0 0;
    overflow: hidden;
    box-shadow: 0 3px 10px rgba(0,0,0,.45);
  }
  .card-front { top: 130px; background: var(--white); }
  .card-back { top: 505px; background: var(--mint); }

  .swoosh { position: absolute; inset: 0; width: 525px; height: 300px; }

  .brand { position: absolute; display: flex; align-items: center; }
  .brand-front { left: 48px; top: 56px; }
  .brand-dot {
    width: 76px; height: 76px; border-radius: 50%;
    background: var(--brand-blue);
    margin-right: 10px;
    flex: none;
  }
  .brand-name { color: var(--brand-blue); font-weight: 400; line-height: 1; }
  .brand-front .brand-name { font-size: 30px; }
  .brand-front .brand-name span { display: block; font-size: 16px; margin-top: 4px; }

  .credential-badge {
    position: absolute; left: 430px; top: 182px;
    width: 73px; height: 36px; background: var(--badge);
  }

  .person { position: absolute; left: 25px; top: 240px; }
  .person-name { color: var(--leaf-light); font-size: 19px; }
  .person-role { color: var(--white); font-size: 14.5px; margin-top: 4px; }

  .contacts {
    position: absolute; right: 22px; top: 226px;
    list-style: none; color: var(--white); font-size: 14px; text-align: right;
  }
  .contacts li { display: flex; justify-content: flex-end; align-items: center; height: 20px; }
  .contacts svg { width: 13px; height: 13px; margin-left: 8px; fill: var(--leaf); }

  .brand-back {
    position: absolute; left: 0; right: 0; top: 26px;
    text-align: center; color: var(--brand-blue); line-height: 1;
  }
  .brand-back .brand-title { font-size: 57px; display: block; }
  .brand-back .brand-sub { font-size: 24px; display: block; margin-top: 2px; }

  .appointment { position: absolute; left: 31px; right: 31px; top: 154px; color: var(--ink); font-size: 14.5px; }
  .field-row { display: flex; align-items: flex-end; height: 22px; margin-bottom: 26px; }
  .field-label { white-space: nowrap; margin-right: 6px; }
  .field-line { flex: 1; border-bottom: 1px solid var(--rule); margin-bottom: 4px; }
  .field-time { margin-left: 16px; }
  .field-line.short { flex: 0 0 112px; }
  .field-suffix { font-size: 11px; margin-left: 6px; margin-bottom: 1px; }

  .website {
    position: absolute; left: 0; right: 0; top: 250px;
    text-align: center; color: var(--ink); font-style: italic;
    font-size: 14px; letter-spacing: 3.6px;
  }
</style>
</head>
<body>

<section class="card card-front" aria-label="Business card front">
  <svg class="swoosh" viewBox="0 0 525 300" aria-hidden="true">
    <defs>
      <radialGradient id="blueField" cx="0.62" cy="0.72" r="0.75">
        <stop offset="0" stop-color="#1f86d6"/>
        <stop offset="0.55" stop-color="#1b4fb0"/>
        <stop offset="1" stop-color="#1f2a80"/>
      </radialGradient>
    </defs>
    <path d="M0,210 Q320,238 525,0 L525,300 L0,300 Z" fill="url(#blueField)"/>
    <path d="M0,181 Q300,222 508,0" fill="none" stroke="#6cbd2a" stroke-width="6"/>
    <path d="M0,196 Q312,234 517,0" fill="none" stroke="#a6d64a" stroke-width="4"/>
  </svg>

  <div class="brand brand-front">
    <div class="brand-dot"></div>
    <p class="brand-name">Brightfield<span>Nutrition &amp; Dietetics</span></p>
  </div>

  <div class="credential-badge" role="img" aria-label="Certified Clinical Nutritionist badge"></div>

  <div class="person">
    <p class="person-name">Marcus Kendrick</p>
    <p class="person-role">Nutritionist &amp; Chef</p>
  </div>

  <ul class="contacts">
    <li>0427 561 903
      <svg viewBox="0 0 24 24"><path d="M6.6 10.8a15 15 0 006.6 6.6l2.2-2.2c.3-.3.7-.4 1-.2 1.1.4 2.3.6 3.6.6.6 0 1 .4 1 1V20c0 .6-.4 1-1 1A17 17 0 013 4c0-.6.4-1 1-1h3.5c.6 0 1 .4 1 1 0 1.3.2 2.5.6 3.6.1.3 0 .7-.2 1z"/></svg>
    </li>
    <li>6457 2183
      <svg viewBox="0 0 24 24"><path d="M6 2h12v5H6zM3 8h18a1 1 0 011 1v8h-4v5H6v-5H2V9a1 1 0 011-1zm5 8v4h8v-4z"/></svg>
    </li>
    <li>marcus.k.diet@fernmail.com
      <svg viewBox="0 0 24 24"><path d="M2 5h20v14H2zm2 2v.5l8 5 8-5V7z"/></svg>
    </li>
  </ul>
</section>

<section class="card card-back" aria-label="Business card back">
  <p class="brand-back">
    <span class="brand-title">Brightfield</span>
    <span class="brand-sub">Nutrition &amp; Dietetics</span>
  </p>

  <div class="appointment">
    <div class="field-row">
      <span class="field-label">Date :</span>
      <span class="field-line"></span>
      <span class="field-label field-time">Time :</span>
      <span class="field-line short"></span>
      <span class="field-suffix">AM/PM</span>
    </div>
    <div class="field-row">
      <span class="field-label">Location :</span>
      <span class="field-line"></span>
    </div>
  </div>

  <p class="website">brightfieldnutrition.com.au</p>
</section>

</body>
</html>
```